Card Design for my dog training business Brightpaw Obedience

Need a business card design for my dog training business with my new logo. Want the card to come off professional yet fun. Want it to be very eye catchy as well. I normally have these at vet clinics, pet stores, and groomers. so need it to look better than my competitors.
Target Market(s)
dog owners
Industry/Entity Type
Dog Training
Contact Information for Business Card
needs logo, my name and info
Font styles to use
Serif
Colors
0255a3
ffffff
ec1f27
000000
333333
fbfbfb
Requirements
Must have
- Brightpaw Obedience
- Felix Orland
- 415 903 2276
- info@brightpawobedience.example
- www.brightpawobedience.example

```html
<!DOCTYPE html>
<html lang="en">
<head>
<meta charset="utf-8">
<title>Brightpaw Obedience – Business Card</title>
<link rel="stylesheet" href="https://fonts.googleapis.com/css2?family=Tinos:ital@0;1&family=Lato:wght@400&display=swap">
<style>
  :root {
    --stage: #ababab;
    --card-light: #ffffff;
    --card-dark: #222222;
    --ink: #111111;
    --ink-soft: #333333;
    --mark-light: #fbfbfb;
    --brand-blue: #0255a3;
    --brand-red: #ec1f27;
  }
  * { margin: 0; padding: 0; box-sizing: border-box; }
  html, body { width: 1200px; height: 900px; overflow: hidden; }
  body { background: var(--stage); position: relative; font-family: "Lato", Arial, sans-serif; }

  .card { position: absolute; top: 200px; width: 310px; height: 502px; }
  .card--front { left: 253px; background: var(--card-light); border-radius: 48px 0 48px 0; }
  .card--back { left: 627px; background: var(--card-dark); border-radius: 0 48px 0 48px; }

  .brand {
    position: absolute; left: 0; right: 0; text-align: center;
    font-family: "Tinos", "Times New Roman", serif; font-weight: 400;
    text-transform: uppercase; letter-spacing: 1px; line-height: 1.15;
    font-size: 30px;
  }
  .brand__dot {
    display: inline-block; width: 12px; height: 12px; border-radius: 50%;
    background: var(--brand-red); margin-right: 8px; vertical-align: 5px;
  }
  .card--front .brand { top: 118px; color: var(--brand-blue); }
  .card--back .brand { top: 196px; color: var(--mark-light); }

  .tagline {
    position: absolute; top: 281px; left: 0; right: 0; text-align: center;
    font-family: "Tinos", "Times New Roman", serif; font-style: italic;
    font-size: 10.5px; color: var(--ink-soft);
  }

  .holder {
    position: absolute; left: 33px; top: 360px;
    font-family: "Tinos", "Times New Roman", serif; font-size: 18px; font-weight: 400;
    letter-spacing: 0.3px; color: var(--ink);
  }

  .contacts { position: absolute; left: 33px; top: 403px; list-style: none; }
  .contacts li {
    display: flex; align-items: center; gap: 5px;
    font-size: 14px; line-height: 18.5px; color: var(--ink);
  }
  .contacts svg { width: 11px; height: 11px; flex: none; fill: var(--brand-blue); }
</style>
</head>
<body>
  <section class="card card--front">
    <div class="brand"><span class="brand__dot"></span>Brightpaw<br>Obedience</div>
    <p class="tagline">“Good habits, happy homes, one dog at a time.”</p>
    <h1 class="holder">FELIX ORLAND</h1>
    <ul class="contacts">
      <li>
        <svg viewBox="0 0 12 12" aria-hidden="true"><path d="M1 4.5C1 3 2.5 2 6 2s5 1 5 2.5v1H8.5V4.2H3.5v1.3H1zM3 6h6l1.5 4.5h-9z"/></svg>
        415 903 2276
      </li>
      <li>
        <svg viewBox="0 0 12 12" aria-hidden="true"><path d="M1 2.5h10v7H1zM1.8 3.3 6 6.6l4.2-3.3z" fill-rule="evenodd"/></svg>
        info@brightpawobedience.example
      </li>
      <li>
        <svg viewBox="0 0 12 12" aria-hidden="true"><circle cx="6" cy="6" r="5"/><path d="M3 4c1 .5 1.5 0 2 1s-1 1.5 0 2.5 1 2 1.5 2.5M7 2.5c.5 1 1.5 1 2.5 1" stroke="#fff" stroke-width="1" fill="none"/></svg>
        www.brightpawobedience.example
      </li>
    </ul>
  </section>

  <section class="card card--back">
    <div class="brand"><span class="brand__dot"></span>Brightpaw<br>Obedience</div>
  </section>
</body>
</html>
```